Tolvik Commercial Cleaning is lookong for a new business card design.

A fresh new design that's professional and stylish. We need a serious upgrade to our business cards. I have included pictures of our existing ones. Our clients include professional individuals and business owners. We woupdblike something professional and upbeat. Please have fun and see what you come uo with.

Target Market(s)

Property managers, business owners, facility managers and other similar professionals

Industry/Entity Type

Janitorial

Contact Information for Business Card

Name, cell, office number, email, web address

Font styles to use
Sans Serif

Colors

Designer to choose colors to be used in the design.

Requirements
Must have
• please use the green color in our logo
Nice to have
• Bar code
Should not have
• Address

```html
<!DOCTYPE html>
<html lang="en">
<head>
<meta charset="utf-8">
<title>Tolvik Commercial Cleaning – Business Card</title>
<link rel="stylesheet" href="https://fonts.googleapis.com/css2?family=Comfortaa:wght@700&family=Open+Sans:wght@400;600&display=swap">
<style>
  :root {
    --backdrop: #2b2b2f;
    --card: #1f1f23;
    --brand-green: #3bb854;
    --brand-blue: #3f70b2;
    --ink-light: #f2f2f2;
    --ghost: #17171a;
  }
  * { box-sizing: border-box; margin: 0; padding: 0; }
  html, body {
    width: 1200px; height: 780px; overflow: hidden;
    background: var(--backdrop);
  }
  .sheet {
    width: 1200px; height: 780px;
    display: flex; align-items: center; justify-content: center; gap: 50px;
  }
  .card {
    position: relative;
    width: 540px; height: 320px;
    background: var(--card);
    border-radius: 26px;
    border-bottom: 3px solid var(--brand-green);
    box-shadow: 0 0 0 1.5px var(--brand-green), 0 18px 40px rgba(0,0,0,.45);
    overflow: hidden;
  }
  .wordmark {
    font-family: "Comfortaa", sans-serif;
    font-weight: 700;
    color: var(--brand-green);
    line-height: 1.05;
    letter-spacing: -0.5px;
  }
  /* front */
  .card--front { display: flex; align-items: center; justify-content: center; }
  .card--front .wordmark { font-size: 46px; text-align: center; }
  /* back */
  .card--back .wordmark {
    position: absolute; left: 40px; top: 70px;
    font-size: 34px;
  }
  .holder {
    position: absolute; right: 34px; top: 28px; text-align: right;
  }
  .holder__name {
    font-family: "Comfortaa", sans-serif; font-weight: 700;
    font-size: 24px; color: var(--brand-blue);
  }
  .holder__role {
    font-family: "Open Sans", sans-serif; font-size: 14px;
    color: var(--ink-light); margin-top: 4px;
  }
  .holder-bar {
    position: absolute; right: 0; top: 22px;
    width: 16px; height: 52px; background: var(--brand-green);
  }
  .ghost-mark {
    position: absolute; right: -20px; bottom: 14px;
    font-family: "Comfortaa", sans-serif; font-weight: 700;
    font-size: 120px; color: var(--ghost); letter-spacing: -4px;
  }
  .contact {
    position: absolute; left: 40px; bottom: 30px;
    list-style: none;
    font-family: "Open Sans", sans-serif; font-size: 14.5px;
    color: var(--ink-light);
  }
  .contact__item { display: flex; align-items: center; gap: 10px; margin-top: 6px; }
  .contact__icon { width: 15px; height: 15px; flex: none; }
</style>
</head>
<body>
<main class="sheet">
  <section class="card card--front" aria-label="Card front">
    <p class="wordmark">Tolvik<br>Commercial Cleaning</p>
  </section>

  <section class="card card--back" aria-label="Card back">
    <span class="ghost-mark" aria-hidden="true">Tolvik</span>
    <div class="holder-bar"></div>
    <div class="holder">
      <p class="holder__name">Mara Lindqvist</p>
      <p class="holder__role">Director</p>
    </div>
    <p class="wordmark">Tolvik<br>Commercial Cleaning</p>
    <ul class="contact">
      <li class="contact__item">
        <svg class="contact__icon" viewBox="0 0 24 24" aria-hidden="true"><path fill="#3bb854" d="M6.6 10.8a15 15 0 0 0 6.6 6.6l2.2-2.2a1 1 0 0 1 1-.25 11.4 11.4 0 0 0 3.6.57 1 1 0 0 1 1 1V20a1 1 0 0 1-1 1A17 17 0 0 1 3 4a1 1 0 0 1 1-1h3.5a1 1 0 0 1 1 1c0 1.25.2 2.45.57 3.57a1 1 0 0 1-.25 1z"/></svg>
        <span>(555) 014-2290</span>
      </li>
      <li class="contact__item">
        <svg class="contact__icon" viewBox="0 0 24 24" aria-hidden="true"><rect x="2" y="5" width="20" height="14" rx="2" fill="#3bb854"/><path d="M3 6l9 7 9-7" fill="none" stroke="#1f1f23" stroke-width="2"/></svg>
        <span>mara@tolvikcleaning.com</span>
      </li>
      <li class="contact__item">
        <svg class="contact__icon" viewBox="0 0 24 24" aria-hidden="true"><circle cx="12" cy="12" r="10" fill="#3bb854"/><path d="M2 12h20M12 2c3 3 3 17 0 20M12 2c-3 3-3 17 0 20" fill="none" stroke="#1f1f23" stroke-width="1.5"/></svg>
        <span>www.tolvikcleaning.com</span>
      </li>
    </ul>
  </section>
</main>
</body>
</html>
```